RW Framewell Inc Business cards

We need business cards using our existing logo but slightly modified. Right now the logo says RW Loadbearing Masonry. We want to keep the RW part of the design, but replace the Structural Concrete portion with "FRAMEWELL". Please see the attached file.
Ideally this would be a blank template so we can add Different Names, titles, and phone numbers later.
On the one side we want only the logo and on the other side the detail. I'm attaching an example for you to see.
Please reach out with any other questions. Our address and other details will be given out once we find a design we like.

Target Market(s)

Construction Industry

```html
<!DOCTYPE html>
<html lang="en">
<head>
<meta charset="utf-8">
<title>RW Framewell Inc – Business Cards</title>
<link href="https://fonts.googleapis.com/css2?family=Montserrat:wght@600;700&family=Roboto:wght@400&display=swap" rel="stylesheet">
<style>
  :root {
    --stage: #5a80bb;
    --brand-blue: #2f5f9f;
    --paper: #f3f3f3;
    --stripe-grey: #6e6e6e;
    --ink-blue: #2c5a97;
    --ink-grey: #6a6a6a;
    --white: #ffffff;
  }
  * { margin: 0; padding: 0; box-sizing: border-box; }
  html, body { width: 1200px; height: 852px; overflow: hidden; }
  body { background: var(--stage); position: relative; }

  .card {
    position: absolute;
    width: 520px;
    height: 300px;
    border-radius: 20px;
    overflow: hidden;
    background: var(--brand-blue);
  }
  .card--front { left: 50px; top: 276px; }
  .card--back { left: 630px; top: 276px; }

  .wordmark {
    position: absolute;
    color: var(--white);
    font-family: "Montserrat", sans-serif;
    font-weight: 700;
    text-align: center;
    line-height: 1;
  }
  .wordmark__initials { display: block; font-size: 86px; letter-spacing: 2px; }
  .wordmark__name { display: block; font-size: 24px; letter-spacing: 6px; margin-top: 8px; }

  .card--front .wordmark { left: 0; right: 0; top: 88px; }
  .card--back .wordmark { right: 34px; top: 166px; }
  .card--back .wordmark__initials { font-size: 62px; }
  .card--back .wordmark__name { font-size: 18px; letter-spacing: 4px; margin-top: 6px; }

  .info-band {
    position: absolute;
    left: 0; top: 0;
    width: 100%;
    height: 134px;
    background: var(--paper);
    border-bottom: 9px solid var(--stripe-grey);
  }
  .person { position: absolute; left: 30px; top: 74px; font-family: "Montserrat", sans-serif; }
  .person__name { color: var(--ink-blue); font-weight: 700; font-size: 20px; }
  .person__title { color: var(--ink-grey); font-weight: 600; font-size: 12px; margin-top: 3px; }

  .contact {
    position: absolute;
    left: 30px; top: 168px;
    color: var(--white);
    font-family: "Roboto", sans-serif;
    font-size: 13px;
    line-height: 19px;
    list-style: none;
  }
  .contact__address { margin-bottom: 8px; }
  .contact__row { display: flex; align-items: center; gap: 10px; }
  .contact__icon { width: 13px; height: 13px; flex: none; }
</style>
</head>
<body>
  <section class="card card--front" aria-label="Card front">
    <div class="wordmark">
      <span class="wordmark__initials">RW</span>
      <span class="wordmark__name">FRAMEWELL</span>
    </div>
  </section>

  <section class="card card--back" aria-label="Card back">
    <div class="info-band">
      <div class="person">
        <p class="person__name">Daniel RW Hart</p>
        <p class="person__title">Managing Director</p>
      </div>
    </div>

    <ul class="contact">
      <li class="contact__address">718 Beamline Rd., Oak Hollow,<br>Nevada, US 654321</li>
      <li class="contact__row">
        <svg class="contact__icon" viewBox="0 0 24 24" aria-hidden="true"><path fill="#fff" d="M6.6 10.8a15 15 0 0 0 6.6 6.6l2.2-2.2c.3-.3.7-.4 1-.2 1.1.4 2.3.6 3.6.6.6 0 1 .4 1 1V20c0 .6-.4 1-1 1A17 17 0 0 1 3 4c0-.6.4-1 1-1h3.5c.6 0 1 .4 1 1 0 1.3.2 2.5.6 3.6.1.3 0 .7-.2 1z"/></svg>
        <span>555-204-7730</span>
      </li>
      <li class="contact__row">
        <svg class="contact__icon" viewBox="0 0 24 24" aria-hidden="true"><path fill="#fff" d="M2 5h20v14H2z"/><path fill="none" stroke="#2f5f9f" stroke-width="2" d="M2 5l10 8 10-8"/></svg>
        <span>daniel@framewellinc.com</span>
      </li>
      <li class="contact__row">
        <svg class="contact__icon" viewBox="0 0 24 24" aria-hidden="true"><circle cx="12" cy="12" r="10" fill="none" stroke="#fff" stroke-width="2"/><path fill="none" stroke="#fff" stroke-width="1.6" d="M2 12h20M12 2c3 3 3 17 0 20M12 2c-3 3-3 17 0 20"/></svg>
        <span>www.framewellinc.com</span>
      </li>
    </ul>

    <div class="wordmark">
      <span class="wordmark__initials">RW</span>
      <span class="wordmark__name">FRAMEWELL</span>
    </div>
  </section>
</body>
</html>
```